Bright Harbor Web Design & Marketing

Will award a 2nd place prize of $100.00 if someone can come up with a logo to match this design!
Updates

Okay, I'm really looking to see some better designs here. What do you think will bring the best designs out? Please remember with all future submissions I'm looking for a cartoon style / illustrator style website. I'm not sure what the technical term is for it, so I uploaded some images in the brief.

Target Market(s)

Small Business Owners

Industry/Entity Type

Marketing

Logo Text

BrightHarbor.com

Number of Pages Required

1 page

Colors

Designer to choose colors to be used in the design.

Requirements
Must have
• Logo should say BrightHarbor.com I would like more than just a text logo. I want some sort of cool custom graphic / icon with it that will look nice on shirts/hats/etc

```html
<!DOCTYPE html>
<html lang="en">
<head>
<meta charset="utf-8">
<title>Bright Harbor Web Design &amp; Marketing</title>
<link href="https://fonts.googleapis.com/css2?family=Exo+2:wght@400;600;700;800&family=Open+Sans:ital,wght@0,400;0,600;0,700;1,400&display=swap" rel="stylesheet">
<style>
:root{
  --green:#8cc152;
  --green-dark:#76a93f;
  --navy:#1f2140;
  --navy-2:#2a2d52;
  --teal:#34b5aa;
  --teal-light:#62cbbf;
  --ink:#2c2c3a;
  --muted:#777a84;
  --line:#e2e4e8;
  --soft:#f1f2f4;
  --white:#ffffff;
  --footer:#22252c;
}
*{box-sizing:border-box;margin:0;padding:0}
html,body{width:1200px;height:4826px;overflow:hidden}
body{font-family:"Open Sans",Arial,sans-serif;color:var(--ink);background:var(--white);position:relative}
.wrap{width:920px;margin:0 auto;position:relative}
section,header,nav,footer{position:absolute;left:0;width:1200px}
.title{font-family:"Exo 2",Arial,sans-serif;font-weight:800;font-size:27px;text-align:center;color:var(--navy);text-transform:uppercase;letter-spacing:.5px}
.title span{color:var(--green)}
.title::after{content:"";display:block;width:46px;height:3px;background:var(--green);margin:9px auto 0}
.btn{display:inline-flex;align-items:center;gap:6px;font-family:"Exo 2",sans-serif;font-weight:700;font-size:12px;color:var(--white);background:var(--green);border-radius:16px;padding:8px 20px;text-transform:uppercase;letter-spacing:.4px}
.btn.navy{background:var(--navy)}

/* header */
.top{top:0;height:90px;background:var(--white)}
.top .wrap{display:flex;align-items:center;justify-content:space-between;height:90px}
.brand{display:flex;align-items:center;gap:12px}
.brand-mark{width:46px;height:46px;background:var(--green);border-radius:6px}
.brand-name{font-family:"Exo 2",sans-serif;font-weight:800;font-size:20px;line-height:1.05;color:var(--navy);text-transform:uppercase}
.top-contact{display:flex;align-items:center;gap:26px}
.phone{display:flex;align-items:center;gap:8px;font-family:"Exo 2",sans-serif;font-weight:700;font-size:17px;color:var(--navy)}
.phone svg{width:26px;height:26px}

.nav{top:90px;height:28px;background:var(--green)}
.nav .wrap{display:flex;justify-content:space-between;height:28px;align-items:stretch}
.nav a{font-family:"Exo 2",sans-serif;font-weight:700;font-size:12px;color:var(--white);text-decoration:none;display:flex;align-items:center;padding:0 32px;text-transform:uppercase}
.nav a.current{background:var(--navy)}

/* hero */
.hero{top:118px;height:472px;background:linear-gradient(120deg,var(--teal) 0%,var(--teal-light) 100%);overflow:hidden}
.hero h1{position:absolute;left:140px;top:162px;font-family:"Exo 2",sans-serif;font-weight:700;font-size:29px;line-height:1.3;color:var(--white);width:420px}
.hero-dots{position:absolute;left:142px;top:298px;display:flex;gap:6px}
.hero-dots i{width:8px;height:8px;border-radius:50%;background:rgba(255,255,255,.5)}
.hero-dots i:first-child{background:var(--white);width:12px;border-radius:4px}
.hero-art{position:absolute;left:600px;top:20px;width:500px;height:452px;border-radius:50% 50% 0 0;background:radial-gradient(circle at 55% 45%,rgba(255,255,255,.38),rgba(255,255,255,.08) 70%)}

/* about */
.about{top:590px;height:263px}
.about .title{margin-top:60px}
.about p{font-size:12.5px;line-height:1.65;text-align:center;color:var(--ink);margin-top:14px}
.about p+p{margin-top:4px}

/* services */
.services{top:853px;height:685px;background:var(--soft)}
.services .title{margin-top:58px}
.svc-grid{display:grid;grid-template-columns:repeat(3,283px);gap:30px 35px;margin-top:36px}
.svc{background:var(--white);border:1px solid var(--line);height:137px;padding:18px 16px;display:grid;grid-template-columns:44px 1fr;column-gap:12px;box-shadow:0 2px 4px rgba(0,0,0,.05)}
.svc svg{width:40px;height:40px}
.svc h3{font-family:"Exo 2",sans-serif;font-weight:700;font-size:15px;line-height:1.2;color:var(--navy)}
.svc p{grid-column:2;font-size:10.5px;line-height:1.5;color:var(--muted);margin-top:8px}

/* pricing */
.pricing{top:1538px;height:659px}
.pricing .title{margin-top:52px}
.plans{position:absolute;left:212px;top:125px;display:flex;align-items:center}
.plan{width:248px;height:430px;background:var(--green);color:var(--white);text-align:center;padding-top:30px}
.plan.pro{width:282px;height:464px;background:var(--navy);border-radius:6px;padding-top:44px;box-shadow:0 6px 16px rgba(0,0,0,.25)}
.plan h3{font-family:"Exo 2",sans-serif;font-weight:700;font-size:26px}
.plan .sub{font-size:10.5px;opacity:.9}
.price{font-family:"Exo 2",sans-serif;font-size:64px;font-weight:400;line-height:1;margin-top:14px;display:flex;justify-content:center;align-items:flex-start;gap:2px}
.price sup{font-size:16px;margin-top:8px}
.price small{font-size:11px;align-self:flex-end;margin-bottom:6px}
.checks{font-size:11.5px;margin:14px 0 6px}
.plan ul{list-style:none}
.plan li{font-size:12px;padding:15px 0;border-top:1px solid rgba(255,255,255,.25);margin:0 22px}
.plan .btn{margin-top:18px}

/* band */
.band{top:2197px;height:254px;background:linear-gradient(90deg,#1c1f26,#3b4150 55%,#22252c)}
.band p{width:860px;margin:88px auto 0;text-align:center;color:var(--white);font-size:13.5px;line-height:1.6}
.band .btn{position:absolute;left:50%;transform:translateX(-50%);top:170px}

/* different */
.different{top:2451px;height:357px}
.different .title{margin-top:58px}
.perks{display:grid;grid-template-columns:repeat(4,1fr);margin-top:34px;text-align:center}
.perk svg{width:72px;height:72px}
.perk h4{font-family:"Exo 2",sans-serif;font-weight:700;font-size:13.5px;color:var(--navy);line-height:1.25;margin:10px auto 6px;width:170px}
.perk p{font-size:10px;line-height:1.5;color:var(--muted);width:180px;margin:0 auto}

/* portfolio */
.portfolio{top:2808px;height:345px;background:var(--soft)}
.portfolio .title{margin-top:55px}
.slider{position:relative}
.shots{display:grid;grid-template-columns:repeat(4,212px);gap:24px;margin-top:34px;justify-content:center}
.shot{height:150px;position:relative;display:flex;align-items:center;justify-content:center}
.shot.a{background:linear-gradient(160deg,#d9dde3,#9aa6b6)}
.shot.b{background:linear-gradient(160deg,#2c5e9e,#e9ecef)}
.shot.c{background:linear-gradient(160deg,#55585f,#2c2e33)}
.shot.d{background:linear-gradient(160deg,#1d8fbf,#7fd0e4)}
.shot .cap{position:absolute;inset:0;background:rgba(31,33,64,.55);display:flex;align-items:center;justify-content:center;color:var(--white);font-family:"Exo 2",sans-serif;font-weight:600;font-size:14px}
.arrow{position:absolute;top:50%;width:26px;height:26px;margin-top:-13px;border-radius:50%;background:var(--white);border:1px solid var(--line);display:flex;align-items:center;justify-content:center}
.arrow svg{width:10px;height:10px}

/* team */
.team{top:3153px;height:611px}
.team .title{margin-top:60px}
.members{display:grid;grid-template-columns:repeat(5,168px);gap:20px;margin-top:30px;justify-content:center}
.member{background:var(--white);border:1px solid var(--line);text-align:center;box-shadow:0 2px 5px rgba(0,0,0,.08)}
.member .photo{width:82px;height:82px;border-radius:50%;margin:14px auto 8px;background:linear-gradient(160deg,#c9ced6,#8a93a2);border:3px solid var(--soft)}
.member h4{font-family:"Exo 2",sans-serif;font-weight:700;font-size:13.5px;color:var(--navy)}
.member p{font-size:10px;color:var(--muted);margin:2px 0 10px}
.member .soc{background:var(--green);height:36px;display:flex;gap:8px;align-items:center;justify-content:center}
.member.active .soc{background:var(--navy)}
.soc i{width:20px;height:20px;border-radius:50%;border:1.5px solid var(--white)}
.bio{margin:20px auto 0;width:868px;background:var(--white);box-shadow:0 2px 8px rgba(0,0,0,.12);padding:16px 20px;font-size:11px;line-height:1.6;color:var(--ink)}
.bio p+p{margin-top:10px}

/* reviews */
.reviews{top:3764px;height:434px;background:var(--soft)}
.reviews .title{margin-top:48px}
.review-row{display:grid;grid-template-columns:1fr 1fr;gap:40px;margin-top:34px}
.review{display:grid;grid-template-columns:92px 1fr;gap:16px}
.review .ava{width:76px;height:76px;border-radius:50%;background:linear-gradient(160deg,#c9ced6,#8a93a2);border:3px solid var(--white);margin:0 auto}
.review .who{text-align:center;font-family:"Exo 2",sans-serif;font-weight:700;font-size:12px;color:var(--navy);margin-top:6px}
.stars{display:flex;justify-content:center;gap:2px;margin-top:3px}
.stars svg{width:10px;height:10px}
.review blockquote{font-style:italic;font-size:11px;line-height:1.6;color:var(--muted);position:relative;padding-top:4px}
.pager{position:absolute;left:140px;top:350px;width:920px;height:1px;background:#cfd2d8}
.pager i{position:absolute;left:460px;top:-9px;width:18px;height:18px;border-radius:50%;background:var(--green);border:4px solid var(--white);box-shadow:0 0 0 1px #cfd2d8}
.pager b{position:absolute;left:438px;top:-6px;width:12px;height:12px;border-radius:50%;background:#cfd2d8}

/* clients */
.clients{top:4198px;height:258px}
.clients .title{margin-top:58px}
.client-row{display:grid;grid-template-columns:repeat(6,138px);gap:10px;justify-content:center;margin-top:32px}
.client{height:78px;border:1px solid var(--line);display:flex;align-items:center;justify-content:center;gap:8px;font-family:"Open Sans",sans-serif;font-weight:700;font-size:17px;color:var(--navy)}
.client i{width:12px;height:12px;border-radius:50%;background:var(--navy)}

/* newsletter */
.newsletter{top:4456px;height:57px;background:var(--green)}
.newsletter .wrap{display:flex;align-items:center;height:57px;gap:14px}
.newsletter svg{width:34px;height:34px}
.newsletter h3{font-family:"Exo 2",sans-serif;font-weight:800;font-size:19px;color:var(--white);text-transform:uppercase;flex:1}
.nl-form{display:flex}
.nl-form span{width:290px;height:30px;background:var(--white);font-size:11px;color:#999;padding:7px 10px}
.nl-form b{height:30px;background:var(--navy);color:var(--white);font-family:"Exo 2",sans-serif;font-size:12px;padding:7px 16px;text-transform:uppercase}

/* footer */
.footer{top:4513px;height:280px;background:linear-gradient(180deg,#2a2e36,#1d2026)}
.foot-grid{display:grid;grid-template-columns:235px 255px 260px 1fr;padding-top:30px}
.footer h5{font-family:"Exo 2",sans-serif;font-weight:700;font-size:13px;color:var(--white);text-transform:uppercase;margin-bottom:14px}
.footer ul{list-style:none}
.footer li{font-size:11px;color:#d0d3d8;margin-bottom:7px;display:flex;gap:8px;align-items:flex-start}
.footer li svg{width:12px;height:12px;flex:none;margin-top:2px}
.field{width:200px;height:26px;background:var(--white);font-size:10px;color:#999;padding:5px 8px;margin-bottom:6px}
.field.tall{height:48px}
.footer .btn{border-radius:2px;padding:5px 14px;font-size:11px}
.foot-brand{display:flex;flex-direction:column;align-items:center;padding-top:10px}
.foot-brand .brand-mark{width:70px;height:70px}
.foot-social{display:flex;gap:6px;margin-top:14px}
.foot-social i{width:20px;height:20px;border-radius:50%;background:var(--green)}
.copyright{position:absolute;left:0;top:4793px;width:1200px;height:33px;background:#15171c;color:#c6c9ce;font-size:11px;text-align:center;line-height:33px}
</style>
</head>
<body>

<header class="top">
  <div class="wrap">
    <div class="brand">
      <div class="brand-mark"></div>
      <div class="brand-name">Bright Harbor<br>Web Design</div>
    </div>
    <div class="top-contact">
      <div class="phone">
        <svg viewBox="0 0 26 26"><circle cx="13" cy="13" r="12" fill="none" stroke="#1f2140" stroke-width="1.6"/><path d="M9 7.5c.6-.6 1.4-.5 1.8.1l1.2 1.8c.3.5.2 1.1-.2 1.5l-.8.7c.7 1.5 1.8 2.6 3.3 3.3l.7-.8c.4-.4 1-.5 1.5-.2l1.8 1.2c.6.4.7 1.2.1 1.8l-1 1c-.9.9-2.3 1-3.5.3-2.4-1.4-4.3-3.3-5.7-5.7-.7-1.2-.6-2.6.3-3.5z" fill="#1f2140"/></svg>
        555.014.2290
      </div>
      <span class="btn">Contact Us Now</span>
    </div>
  </div>
</header>

<nav class="nav">
  <div class="wrap">
    <a class="current">Home</a>
    <a>Services &amp; Pricing</a>
    <a>Our Team</a>
    <a>Clients/Portfolio</a>
    <a>Contact Us</a>
  </div>
</nav>

<section class="hero">
  <h1>The Design &amp; Marketing Team That Always Puts Trust &amp; Loyalty Before Profits</h1>
  <div class="hero-dots"><i></i><i></i><i></i></div>
  <div class="hero-art" role="img" aria-label="Illustration of a hand holding an SEO magnifying glass surrounded by colourful web marketing icons"></div>
</section>

<section class="about">
  <div class="wrap">
    <h2 class="title">About <span>Bright Harbor</span> Web Design</h2>
    <p>We believe that honesty and integrity come before personal profits. We are a family owned and operated company. Our parents raised us to take care of each other and that's exactly what we've done. We treat each of our clients with the same loyalty and respect that we give each other.</p>
    <p>We are not looking to have hundreds and hundreds of clients. We are looking to expand our family with a handful of like-minded individuals. Companies who take pride in their work and their customers. We want to build mutually beneficial, lucrative, and long term partnerships.</p>
  </div>
</section>

<section class="services">
  <div class="wrap">
    <h2 class="title">Our <span>Services</span></h2>
    <div class="svc-grid">
      <div class="svc"><svg viewBox="0 0 40 40" fill="none" stroke="#8cc152" stroke-width="2"><rect x="4" y="7" width="32" height="22" rx="2"/><path d="M14 35h12M20 29v6M10 22l8-8 5 5"/></svg><h3>Website Design<br>&amp; Management</h3><p>Lorem ipsum dolor sit amet, consectetur adipiscing elit, sed diam nonummy nibh euismod tincidunt ut laoreet.</p></div>
      <div class="svc"><svg viewBox="0 0 40 40" fill="none" stroke="#8cc152" stroke-width="2"><rect x="5" y="5" width="30" height="30" rx="3"/><rect x="11" y="11" width="8" height="8"/><path d="M23 12h7M23 17h7M11 25h19M11 30h12"/></svg><h3>Logo Design<br>&amp; Branding Materials</h3><p>Lorem ipsum dolor sit amet, consectetur adipiscing elit, sed diam nonummy nibh euismod tincidunt ut laoreet.</p></div>
      <div class="svc"><svg viewBox="0 0 40 40" fill="none" stroke="#8cc152" stroke-width="2"><path d="M5 14h30l-3 20H8z"/><path d="M14 14V10a6 6 0 0 1 12 0v4"/></svg><h3>Online Store Design<br>&amp; Management</h3><p>Lorem ipsum dolor sit amet, consectetur adipiscing elit, sed diam nonummy nibh euismod tincidunt ut laoreet.</p></div>
      <div class="svc"><svg viewBox="0 0 40 40" fill="none" stroke="#8cc152" stroke-width="2"><path d="M20 36s11-11 11-20a11 11 0 0 0-22 0c0 9 11 20 11 20z"/><circle cx="20" cy="16" r="4"/></svg><h3>Local<br>SEO Management</h3><p>Lorem ipsum dolor sit amet, consectetur adipiscing elit, sed diam nonummy nibh euismod tincidunt ut laoreet.</p></div>
      <div class="svc"><svg viewBox="0 0 40 40" fill="none" stroke="#8cc152" stroke-width="2"><circle cx="17" cy="17" r="11"/><path d="M25 25l10 10M11 20l4-4 3 3 5-6"/></svg><h3>Search Engine<br>Optimization</h3><p>Lorem ipsum dolor sit amet, consectetur adipiscing elit, sed diam nonummy nibh euismod tincidunt ut laoreet.</p></div>
      <div class="svc"><svg viewBox="0 0 40 40" fill="none" stroke="#8cc152" stroke-width="2"><circle cx="10" cy="20" r="5"/><circle cx="30" cy="9" r="5"/><circle cx="30" cy="31" r="5"/><path d="M14.5 17.5l11-6M14.5 22.5l11 6"/></svg><h3>Social Media<br>Marketing</h3><p>Lorem ipsum dolor sit amet, consectetur adipiscing elit, sed diam nonummy nibh euismod tincidunt ut laoreet.</p></div>
      <div class="svc"><svg viewBox="0 0 40 40" fill="none" stroke="#8cc152" stroke-width="2"><path d="M11 14V5h18v9"/><rect x="5" y="14" width="30" height="14" rx="2"/><path d="M11 24h18v11H11z"/></svg><h3>Marketing<br>Material &amp; Print Design</h3><p>Lorem ipsum dolor sit amet, consectetur adipiscing elit, sed diam nonummy nibh euismod tincidunt ut laoreet.</p></div>
      <div class="svc"><svg viewBox="0 0 40 40" fill="none" stroke="#8cc152" stroke-width="2"><circle cx="20" cy="20" r="14"/><path d="M20 6v28M6 20h28M10 10c6 5 14 5 20 0M10 30c6-5 14-5 20 0"/></svg><h3>Outsourcing<br>Management</h3><p>Lorem ipsum dolor sit amet, consectetur adipiscing elit, sed diam nonummy nibh euismod tincidunt ut laoreet.</p></div>
      <div class="svc"><svg viewBox="0 0 40 40" fill="none" stroke="#8cc152" stroke-width="2"><path d="M5 8h22v14H14l-6 5v-5H5z"/><path d="M30 15h5v14h-3v5l-6-5h-9v-4"/></svg><h3>Consulting<br>Service</h3><p>Lorem ipsum dolor sit amet, consectetur adipiscing elit, sed diam nonummy nibh euismod tincidunt ut laoreet.</p></div>
    </div>
  </div>
</section>

<section class="pricing">
  <h2 class="title">Plans <span>&amp;</span> Pricing</h2>
  <div class="plans">
    <div class="plan">
      <h3>Free</h3><div class="sub">Personal Website or Blog</div>
      <div class="price"><sup>$</sup>0<small>/mo</small></div>
      <div class="checks">25 checks</div>
      <ul><li>Lorem Ipsum Dolor Sit Amet</li><li>Sed Diam Nonummy Nibh</li><li>Laoreet Dolore Magna Aliquam</li></ul>
      <span class="btn navy">Get Started &raquo;</span>
    </div>
    <div class="plan pro">
      <h3>Professional</h3><div class="sub">The All Inclusive Suite</div>
      <div class="price"><sup>$</sup>199<small>/mo</small></div>
      <div class="checks">250 checks</div>
      <ul><li>Sed Diam Nonummy Nibh</li><li>Lorem Ipsum Dolor Sit Amet</li><li>Laoreet Dolore Magna</li></ul>
      <span class="btn">Get Started &raquo;</span>
    </div>
    <div class="plan">
      <h3>Enterprise</h3><div class="sub">For Extensive Monitoring</div>
      <div class="price"><sup>$</sup>499<small>/mo</small></div>
      <div class="checks">1000+ checks</div>
      <ul><li>Lorem Ipsum Dolor Sit Amet</li><li>Sed Diam Nonummy Nibh</li><li>Laoreet Dolore Magna Aliquam</li></ul>
      <span class="btn navy">Get Started &raquo;</span>
    </div>
  </div>
</section>

<section class="band" role="img" aria-label="Darkened photo of a business meeting at a desk">
  <p>Lorem ipsum dolor sit amet, consectetur adipiscing elit, sed diam nonummy nibh euismod tincidunt ut laoreet dolore magna aliquam erat volutpat. Ut wisi enim ad minim veniam, quis nostrud exerci tation ullamcorper.</p>
  <span class="btn">Contact Us Now &raquo;</span>
</section>

<section class="different">
  <div class="wrap">
    <h2 class="title">What Makes <span>Me Different?</span></h2>
    <div class="perks">
      <div class="perk"><svg viewBox="0 0 72 72"><circle cx="36" cy="36" r="33" fill="#fff" stroke="#8cc152" stroke-width="3"/><path d="M36 20l15 27H21z" fill="none" stroke="#1f2140" stroke-width="2.5"/><path d="M36 30v8M36 42v2" stroke="#1f2140" stroke-width="2.5"/></svg><h4>100% Risk Free Investment</h4><p>If we are unable to deliver anything that we say we can we will refund you 100% of your investment</p></div>
      <div class="perk"><svg viewBox="0 0 72 72"><circle cx="36" cy="36" r="33" fill="#fff" stroke="#8cc152" stroke-width="3"/><rect x="20" y="25" width="32" height="22" rx="3" fill="none" stroke="#1f2140" stroke-width="2.5"/><path d="M20 32h32" stroke="#1f2140" stroke-width="4"/></svg><h4>Customer Loyalty Program</h4><p>After 12 months of on-time payments, customers will receive cash back reward bonuses</p></div>
      <div class="perk"><svg viewBox="0 0 72 72"><circle cx="36" cy="36" r="33" fill="#fff" stroke="#8cc152" stroke-width="3"/><rect x="22" y="22" width="28" height="28" rx="3" fill="none" stroke="#1f2140" stroke-width="2.5"/><path d="M28 36l6 6 11-12" fill="none" stroke="#1f2140" stroke-width="2.5"/></svg><h4>Unmatched Personal Service</h4><p>Do you need us to come to your office to help train staff on the management of your new site</p></div>
      <div class="perk"><svg viewBox="0 0 72 72"><circle cx="36" cy="36" r="33" fill="#fff" stroke="#8cc152" stroke-width="3"/><rect x="24" y="20" width="24" height="32" rx="3" fill="none" stroke="#1f2140" stroke-width="2.5"/><path d="M29 29h14M29 35h14M29 41h8" stroke="#1f2140" stroke-width="2.5"/></svg><h4>Multiple Payment Options Available</h4><p>Website Leasing, 90 Days Same As Cash, Website Financing</p></div>
    </div>
  </div>
</section>

<section class="portfolio">
  <div class="wrap">
    <h2 class="title">Work <span>Portfolio</span></h2>
    <div class="slider">
      <div class="shots">
        <div class="shot a" role="img" aria-label="Website mockup shown on a desktop screen"></div>
        <div class="shot b" role="img" aria-label="Branded stationery set"></div>
        <div class="shot c" role="img" aria-label="Business card design on a dark surface"><div class="cap">Laoreet Dolore Magna</div></div>
        <div class="shot d" role="img" aria-label="Website shown on a laptop and phone"></div>
      </div>
      <span class="arrow" style="left:-30px"><svg viewBox="0 0 10 10"><path d="M7 1L3 5l4 4" fill="none" stroke="#777" stroke-width="1.5"/></svg></span>
      <span class="arrow" style="right:-30px"><svg viewBox="0 0 10 10"><path d="M3 1l4 4-4 4" fill="none" stroke="#777" stroke-width="1.5"/></svg></span>
    </div>
  </div>
</section>

<section class="team">
  <div class="wrap">
    <h2 class="title">Our <span>Team</span></h2>
    <div class="slider">
      <div class="members">
        <div class="member"><div class="photo" role="img" aria-label="Team member portrait"></div><h4>Evan Marsh</h4><p>Chief Executive Officer</p><div class="soc"><i></i><i></i><i></i></div></div>
        <div class="member active"><div class="photo" role="img" aria-label="Team member portrait"></div><h4>Evan Marsh</h4><p>Chief Operation Officer</p><div class="soc"><i></i><i></i><i></i></div></div>
        <div class="member active"><div class="photo" role="img" aria-label="Team member portrait"></div><h4>Evan Marsh</h4><p>Chief Technical Officer</p><div class="soc"><i></i><i></i><i></i></div></div>
        <div class="member active"><div class="photo" role="img" aria-label="Team member portrait"></div><h4>Evan Marsh</h4><p>Chief Executive Officer</p><div class="soc"><i></i><i></i><i></i></div></div>
        <div class="member active"><div class="photo" role="img" aria-label="Team member portrait"></div><h4>Evan Marsh</h4><p>Chief Executive Officer</p><div class="soc"><i></i><i></i><i></i></div></div>
      </div>
      <span class="arrow" style="left:-30px"><svg viewBox="0 0 10 10"><path d="M7 1L3 5l4 4" fill="none" stroke="#777" stroke-width="1.5"/></svg></span>
      <span class="arrow" style="right:-30px"><svg viewBox="0 0 10 10"><path d="M3 1l4 4-4 4" fill="none" stroke="#777" stroke-width="1.5"/></svg></span>
    </div>
    <div class="bio">
      <p>Lorem ipsum dolor sit amet, consectetuer adipiscing elit, sed diam nonummy nibh euismod tincidunt ut laoreet dolore magna aliquam erat volutpat. Ut wisi enim ad minim veniam, quis nostrud exerci tation ullamcorper suscipit lobortis nisl ut aliquip ex ea commodo consequat. Duis autem vel eum iriure dolor in hendrerit in vulputate velit esse molestie consequat, vel illum dolore eu feugiat nulla facilisis at vero eros et accumsan et iusto odio dignissim qui blandit praesent luptatum zzril delenit augue duis dolore te feugait nulla facilisi.</p>
      <p>Lorem ipsum dolor sit amet, consectetuer adipiscing elit, sed diam nonummy nibh euismod tincidunt ut laoreet dolore magna aliquam erat volutpat. Ut wisi enim ad minim veniam, quis nostrud exerci tation ullamcorper suscipit lobortis nisl ut aliquip ex ea commodo consequat. Duis autem vel eum iriure dolor in hendrerit in vulputate velit esse molestie consequat, vel illum dolore eu feugiat nulla facilisis at vero eros et accumsan et iusto odio dignissim qui blandit praesent luptatum zzril delenit augue duis dolore te feugait nulla facilisi.</p>
    </div>
  </div>
</section>

<section class="reviews">
  <div class="wrap">
    <h2 class="title">Client <span>Reviews</span></h2>
    <div class="review-row">
      <div class="review">
        <div><div class="ava" role="img" aria-label="Client portrait"></div><div class="who">Lorem Ipsum</div>
          <div class="stars"><svg viewBox="0 0 10 10"><path d="M5 0l1.5 3.3 3.5.4-2.6 2.4.7 3.5L5 7.8 1.9 9.6l.7-3.5L0 3.7l3.5-.4z" fill="#f5a623"/></svg><svg viewBox="0 0 10 10"><path d="M5 0l1.5 3.3 3.5.4-2.6 2.4.7 3.5L5 7.8 1.9 9.6l.7-3.5L0 3.7l3.5-.4z" fill="#f5a623"/></svg><svg viewBox="0 0 10 10"><path d="M5 0l1.5 3.3 3.5.4-2.6 2.4.7 3.5L5 7.8 1.9 9.6l.7-3.5L0 3.7l3.5-.4z" fill="#f5a623"/></svg><svg viewBox="0 0 10 10"><path d="M5 0l1.5 3.3 3.5.4-2.6 2.4.7 3.5L5 7.8 1.9 9.6l.7-3.5L0 3.7l3.5-.4z" fill="#f5a623"/></svg><svg viewBox="0 0 10 10"><path d="M5 0l1.5 3.3 3.5.4-2.6 2.4.7 3.5L5 7.8 1.9 9.6l.7-3.5L0 3.7l3.5-.4z" fill="#ccc"/></svg></div></div>
        <blockquote>&ldquo; Lorem ipsum dolor sit amet, consectetuer adipiscing elit, sed diam nonummy nibh euismod tincidunt ut laoreet dolore magna aliquam erat volutpat. Ut wisi enim ad minim veniam, quis nostrud exerci tation ullamcorper suscipit lobortis nisl ut aliquip ex ea commodo consequat. Duis autem vel eum iriure dolor in hendrerit in vulputate velit esse molestie consequat, vel illum dolore eu feugiat nulla facilisis. &rdquo;</blockquote>
      </div>
      <div class="review">
        <div><div class="ava" role="img" aria-label="Client portrait"></div><div class="who">Lorem Ipsum</div>
          <div class="stars"><svg viewBox="0 0 10 10"><path d="M5 0l1.5 3.3 3.5.4-2.6 2.4.7 3.5L5 7.8 1.9 9.6l.7-3.5L0 3.7l3.5-.4z" fill="#f5a623"/></svg><svg viewBox="0 0 10 10"><path d="M5 0l1.5 3.3 3.5.4-2.6 2.4.7 3.5L5 7.8 1.9 9.6l.7-3.5L0 3.7l3.5-.4z" fill="#f5a623"/></svg><svg viewBox="0 0 10 10"><path d="M5 0l1.5 3.3 3.5.4-2.6 2.4.7 3.5L5 7.8 1.9 9.6l.7-3.5L0 3.7l3.5-.4z" fill="#f5a623"/></svg><svg viewBox="0 0 10 10"><path d="M5 0l1.5 3.3 3.5.4-2.6 2.4.7 3.5L5 7.8 1.9 9.6l.7-3.5L0 3.7l3.5-.4z" fill="#f5a623"/></svg><svg viewBox="0 0 10 10"><path d="M5 0l1.5 3.3 3.5.4-2.6 2.4.7 3.5L5 7.8 1.9 9.6l.7-3.5L0 3.7l3.5-.4z" fill="#ccc"/></svg></div></div>
        <blockquote>&ldquo; Lorem ipsum dolor sit amet, consectetuer adipiscing elit, sed diam nonummy nibh euismod tincidunt ut laoreet dolore magna aliquam erat volutpat. Ut wisi enim ad minim veniam, quis nostrud exerci tation ullamcorper suscipit lobortis nisl ut aliquip ex ea commodo consequat. Duis autem vel eum iriure dolor in hendrerit in vulputate velit esse molestie consequat, vel illum dolore eu feugiat nulla facilisis. &rdquo;</blockquote>
      </div>
    </div>
  </div>
  <div class="pager"><b></b><i></i></div>
</section>

<section class="clients">
  <div class="wrap">
    <h2 class="title">Our <span>Clients</span></h2>
    <div class="slider">
      <div class="client-row">
        <div class="client"><i></i>Northvale</div>
        <div class="client">Lumora</div>
        <div class="client"><i></i>Kestrel</div>
        <div class="client"><i></i>Oakline</div>
        <div class="client">Pinecrest</div>
        <div class="client">Lumora</div>
      </div>
      <span class="arrow" style="left:-34px;border:none;background:none"><svg viewBox="0 0 10 10"><path d="M7 1L3 5l4 4" fill="none" stroke="#1f2140" stroke-width="1.5"/></svg></span>
      <span class="arrow" style="right:-34px;border:none;background:none"><svg viewBox="0 0 10 10"><path d="M3 1l4 4-4 4" fill="none" stroke="#1f2140" stroke-width="1.5"/></svg></span>
    </div>
  </div>
</section>

<section class="newsletter">
  <div class="wrap">
    <svg viewBox="0 0 34 34"><rect x="3" y="9" width="28" height="19" rx="2" fill="#fff"/><path d="M3 10l14 10 14-10" fill="none" stroke="#76a93f" stroke-width="2"/></svg>
    <h3>Subscribe Our Newsletter</h3>
    <div class="nl-form"><span>Enter Your Email Address</span><b>Subscribe &raquo;</b></div>
  </div>
</section>

<footer class="footer">
  <div class="wrap foot-grid">
    <div>
      <h5>Quick Links</h5>
      <ul><li>Home</li><li>Services &amp; Pricing</li><li>Our Team</li><li>Clients/Portfolio</li><li>Contact Us</li></ul>
    </div>
    <div>
      <h5>Contact Details</h5>
      <ul>
        <li><svg viewBox="0 0 12 12"><path d="M6 11S2 7 2 4.5a4 4 0 0 1 8 0C10 7 6 11 6 11z" fill="#8cc152"/></svg><span>Bright Harbor Web Design<br>0000 Harbor Lane, Suite 1<br>Anytown, ST 00000</span></li>
        <li><svg viewBox="0 0 12 12"><path d="M3 1.5l2 2.2-1 1.2a6 6 0 0 0 3 3l1.2-1 2.2 2-1.2 1.6C5.5 10.2 1.8 6.5 1.5 2.7z" fill="#8cc152"/></svg>555.014.2290</li>
        <li><svg viewBox="0 0 12 12"><path d="M3 1.5l2 2.2-1 1.2a6 6 0 0 0 3 3l1.2-1 2.2 2-1.2 1.6C5.5 10.2 1.8 6.5 1.5 2.7z" fill="#8cc152"/></svg>555.014.2291</li>
        <li><svg viewBox="0 0 12 12"><rect x="1" y="2.5" width="10" height="7" fill="#8cc152"/></svg>info@brightharbor.com</li>
      </ul>
    </div>
    <div>
      <h5>Quick Inquiry</h5>
      <div class="field">Name</div>
      <div class="field">Email</div>
      <div class="field tall">Message</div>
      <span class="btn">Submit &raquo;</span>
    </div>
    <div class="foot-brand">
      <div class="brand-mark"></div>
      <div class="foot-social"><i></i><i></i><i></i><i></i></div>
    </div>
  </div>
</footer>
<div class="copyright">Copyright &copy; 2017 BRIGHT HARBOR WEB DESIGN. All Rights Reserved.</div>

</body>
</html>
```